Brightfen Business Card Redesign & Logo Update

We need to update our business cards to something more modern and fresh. Brightfen can provide the current color schemes and old design examples, but welcome creativity in helping us with this redesign. PLEASE NOTE that we no longer utilize the "tree" and/or "leaf" imagery in our branding. If able would apprecaite an update on the quality of our "words only" logo in Ai. / PNG formats too.

Target Market(s)

Investors, landowners, corporate partners, contractors

Industry/Entity Type

Environmental Restoration & Conservation

Contact Information for Business Card

Logo, persons name, title, mailing address, phone and email, website url

Font styles to use
Other font styles liked:
• Merriweather

Requirements
Nice to have
• Logo, persons name, title, mailing address, phone and email, website url, but open to ideams
Should not have
• No all back backgrounds

```html
<!DOCTYPE html>
<html lang="en">
<head>
<meta charset="UTF-8">
<title>Brightfen Business Card</title>
<link rel="stylesheet" href="https://fonts.googleapis.com/css2?family=Merriweather:wght@400;700;900&display=swap">
<style>
  :root {
    --backdrop: #a4a4a4;
    --card: #ffffff;
    --orange: #e87d24;
    --green: #1a7a3c;
    --ink: #1b1b1b;
  }
  * { margin: 0; padding: 0; box-sizing: border-box; }
  html, body {
    width: 1146px;
    height: 1200px;
    overflow: hidden;
    background: var(--backdrop);
    font-family: "Merriweather", Georgia, serif;
    color: var(--ink);
  }
  .card {
    position: absolute;
    left: 176px;
    width: 797px;
    background: var(--card);
  }
  .card-front { top: 113px; height: 455px; }
  .card-back { top: 595px; height: 468px; }

  .wordmark {
    font-family: "Merriweather", Georgia, serif;
    font-weight: 900;
    color: var(--green);
    letter-spacing: 1px;
    line-height: 1;
    white-space: nowrap;
  }
  .card-front .wordmark {
    position: absolute;
    left: 0; right: 0;
    top: 270px;
    text-align: center;
    font-size: 60px;
  }
  .card-back .wordmark {
    position: absolute;
    right: 34px;
    top: 68px;
    font-size: 44px;
  }

  .person {
    position: absolute;
    left: 34px;
    top: 64px;
  }
  .person-name {
    font-size: 28px;
    font-weight: 700;
    letter-spacing: 0.5px;
  }
  .person-name .first { color: var(--orange); }
  .person-name .last { color: var(--green); }
  .person-title {
    font-size: 21px;
    margin-top: 4px;
  }

  .contact {
    position: absolute;
    left: 34px;
    top: 320px;
    list-style: none;
    font-size: 22px;
  }
  .contact li {
    display: flex;
    align-items: center;
    height: 28px;
    white-space: nowrap;
  }
  .contact svg {
    width: 16px;
    height: 16px;
    margin-right: 10px;
    fill: var(--orange);
  }

  .address {
    position: absolute;
    right: 34px;
    top: 348px;
    text-align: right;
    font-size: 22px;
    font-style: normal;
    line-height: 28px;
    white-space: nowrap;
  }

  .band {
    position: absolute;
    left: 0;
    bottom: 0;
    width: 797px;
    height: 30px;
    display: block;
  }
</style>
</head>
<body>

  <section class="card card-front">
    <div class="wordmark">BRIGHTFEN</div>
  </section>

  <section class="card card-back">
    <div class="person">
      <div class="person-name"><span class="first">NOLAN</span> <span class="last">HARTE</span></div>
      <div class="person-title">Founder</div>
    </div>

    <div class="wordmark">BRIGHTFEN</div>

    <ul class="contact">
      <li>
        <svg viewBox="0 0 16 16" aria-hidden="true"><path d="M3 2h3l1.5 3.5-2 1.3a8 8 0 0 0 3.7 3.7l1.3-2L14 10v3a1 1 0 0 1-1 1A11 11 0 0 1 2 3a1 1 0 0 1 1-1z"/></svg>
        (555) 014-2290
      </li>
      <li>
        <svg viewBox="0 0 16 16" aria-hidden="true"><path d="M1 3h14v10H1z"/><path d="M1 3l7 5 7-5" fill="none" stroke="#fff" stroke-width="1.4"/></svg>
        hello@brightfen.net
      </li>
      <li>
        <svg viewBox="0 0 16 16" aria-hidden="true"><circle cx="8" cy="8" r="7"/><path d="M1 8h14M8 1c-3 3.5-3 10.5 0 14M8 1c3 3.5 3 10.5 0 14" fill="none" stroke="#fff" stroke-width="1.2"/></svg>
        www.brightfen.net
      </li>
    </ul>

    <address class="address">
      Brightfen Head Office<br>
      Rte No. 48, PO 7120, OR
    </address>

    <svg class="band" viewBox="0 0 797 30" preserveAspectRatio="none" aria-hidden="true">
      <rect x="0" y="0" width="797" height="30" fill="var(--orange)"/>
      <polygon points="438,0 626,0 607,30 418,30" fill="var(--green)"/>
      <polygon points="626,0 634,0 615,30 607,30" fill="#ffffff"/>
    </svg>
  </section>

</body>
</html>
```